A new presentation to our clients

we are a Real Estate agency, our website is www.lumibrasa.com and it’s time to have a new, fashion and remarcable Business Card. we want to differentiate ourselves from other companies so we want a business card that differentiates us. we want the business card to impact our customers. in the competitive market that we have today, we have to be different and it is this difference that we seek

Target Market(s)

Real Estate Clients

Contact Information for Business Card

We search a totaly diferent card from the usual

Font styles to use
Sans Serif

Colors
e34197

Requirements
Must have
• Logo, adress, phone contact, e-mail, photo, and our website
Nice to have
• We would like to see a modern business card
Should not have
• Houses or building draws

```html
<!DOCTYPE html>
<html lang="en">
<head>
<meta charset="utf-8">
<title>Lumibrasa Business Card</title>
<link rel="stylesheet" href="https://fonts.googleapis.com/css2?family=Bebas+Neue&family=Lato:wght@400;700&display=swap">
<style>
  :root {
    --stage: #2b2b2e;
    --card-dark: #474a53;
    --brand-pink: #e8317a;
    --pink-light: #ee5a92;
    --pink-deep: #d6326f;
    --text-light: #f2f2f4;
  }
  html, body {
    margin: 0;
    padding: 0;
    width: 1200px;
    height: 1200px;
    overflow: hidden;
    background: var(--stage);
  }
  .canvas {
    position: relative;
    width: 1200px;
    height: 1200px;
  }
  .card {
    position: absolute;
    left: 140px;
    width: 920px;
    height: 525px;
    border-radius: 32px;
    overflow: hidden;
  }
  .card--front {
    top: 48px;
    background: var(--card-dark);
  }
  .card--back {
    top: 640px;
    background: var(--brand-pink);
  }
  .identity {
    position: absolute;
    right: 494px;
    top: 220px;
    text-align: right;
  }
  .identity__name {
    font-family: "Bebas Neue", sans-serif;
    font-size: 52px;
    line-height: 1;
    color: var(--text-light);
    letter-spacing: 0.5px;
  }
  .identity__role {
    font-family: "Lato", sans-serif;
    font-size: 25px;
    line-height: 1;
    margin-top: 2px;
    color: var(--brand-pink);
  }
  .contacts {
    position: absolute;
    left: 494px;
    top: 220px;
    margin: 0;
    padding: 0;
    list-style: none;
  }
  .contacts__item {
    display: flex;
    align-items: center;
    height: 29.5px;
    font-family: "Lato", sans-serif;
    font-size: 21px;
    color: var(--text-light);
  }
  .contacts__icon {
    width: 20px;
    height: 20px;
    margin-right: 20px;
    flex: none;
  }
  .address {
    position: absolute;
    left: 0;
    right: 0;
    top: 455px;
    text-align: center;
    font-family: "Lato", sans-serif;
    font-size: 21px;
    color: var(--text-light);
  }
  .card__texture {
    position: absolute;
    inset: 0;
    background:
      radial-gradient(ellipse 60% 30% at 30% 45%, var(--pink-light), transparent 70%),
      radial-gradient(ellipse 50% 25% at 75% 70%, var(--pink-deep), transparent 70%),
      radial-gradient(ellipse 40% 20% at 60% 20%, var(--pink-light), transparent 70%),
      var(--brand-pink);
  }
  .brand-name {
    position: absolute;
    left: 0;
    right: 0;
    top: 185px;
    text-align: center;
    font-family: "Lato", sans-serif;
    font-weight: 700;
    font-size: 134px;
    line-height: 1;
    color: #ffffff;
  }
</style>
</head>
<body>
<main class="canvas">
  <section class="card card--front">
    <div class="identity">
      <div class="identity__name">RAFAEL DUARTE</div>
      <div class="identity__role">CEO/manager</div>
    </div>
    <ul class="contacts">
      <li class="contacts__item">
        <svg class="contacts__icon" viewBox="0 0 20 20"><rect x="5" y="1" width="10" height="18" rx="2" fill="none" stroke="var(--brand-pink)" stroke-width="1.8"/><circle cx="10" cy="16" r="1" fill="var(--brand-pink)"/></svg>
        +321 - 654 - 7108
      </li>
      <li class="contacts__item">
        <svg class="contacts__icon" viewBox="0 0 20 20"><rect x="1" y="4" width="18" height="12" fill="var(--brand-pink)"/><path d="M1 4 L10 11 L19 4" fill="none" stroke="var(--card-dark)" stroke-width="1.5"/></svg>
        hello@lumibrasa.com
      </li>
      <li class="contacts__item">
        <svg class="contacts__icon" viewBox="0 0 20 20" fill="none" stroke="var(--brand-pink)" stroke-width="1.3"><circle cx="10" cy="10" r="8"/><ellipse cx="10" cy="10" rx="3.5" ry="8"/><path d="M2 10 H18 M3.5 6 H16.5 M3.5 14 H16.5"/></svg>
        www.lumibrasa.com
      </li>
    </ul>
    <div class="address">Rua das Palmeiras 2480 Jardim Sul Campinas, Brazil</div>
  </section>

  <section class="card card--back">
    <div class="card__texture" role="img" aria-label="Abstract flowing pink marble texture"></div>
    <div class="brand-name">Lumibrasa</div>
  </section>
</main>
</body>
</html>
```